I need a new business card designed, we recently rebranded and I need to get a fresh design to match our new logo, colours and branding.

Details:

Derek Havill | Founder & CEO
Address: 7 Marlowfern Lane, #09-14 Tavenport Crest, Singapore 318547
Tel: +65 93568214
Web: www.frostkarta.com.sg
hello@frostkarta.com.sg

I've attached my old card as well

Industry/Entity Type

Business

Requirements
Must have
• Front and Back
Interesting use of logo
Correct use of colour scheme

```html
<!DOCTYPE html>
<html lang="en">
<head>
<meta charset="utf-8">
<title>frostkarta business card</title>
<link rel="stylesheet" href="https://fonts.googleapis.com/css2?family=Source+Sans+3:wght@400;600;700&display=swap">
<style>
  :root {
    --stage: #ece9e5;
    --card: #ffffff;
    --brand-blue: #00a6e6;
    --name-blue: #2cb3ea;
    --ink-warm: #6e625b;
    --ink-label: #5a4f49;
    --rule: #4a4a4a;
    --mist: #dcf2fc;
    --card-shadow: 0 4px 14px rgba(0,0,0,0.28);
  }
  * { box-sizing: border-box; margin: 0; padding: 0; }
  html, body { width: 1200px; height: 1000px; overflow: hidden; }
  body {
    position: relative;
    background: var(--stage);
    font-family: "Source Sans 3", "Helvetica Neue", Arial, sans-serif;
  }
  .card {
    position: absolute;
    width: 728px;
    height: 416px;
    background: var(--card);
    box-shadow: var(--card-shadow);
    overflow: hidden;
  }
  .card--back { left: 381px; top: 99px; }
  .card--front { left: 129px; top: 427px; }

  .brand { position: absolute; display: flex; align-items: center; }
  .brand__dot { border-radius: 50%; background: var(--brand-blue); flex: none; }
  .brand__text { display: flex; flex-direction: column; }
  .brand__name { color: var(--ink-warm); font-weight: 600; line-height: 1; letter-spacing: -0.5px; }
  .brand__tagline { color: var(--brand-blue); font-weight: 700; line-height: 1; letter-spacing: 0.3px; }

  .card--back .brand { left: 221px; top: 161px; }
  .card--back .brand__dot { width: 78px; height: 78px; margin-right: 12px; }
  .card--back .brand__name { font-size: 50px; }
  .card--back .brand__tagline { font-size: 12.5px; margin-top: 7px; }

  .card--front .brand { left: 46px; top: 42px; }
  .card--front .brand__dot { width: 40px; height: 40px; margin-right: 7px; }
  .card--front .brand__name { font-size: 27px; }
  .card--front .brand__tagline { font-size: 6.5px; margin-top: 3px; }

  .holder { position: absolute; left: 457px; top: 28px; }
  .holder__name { color: var(--name-blue); font-size: 36px; font-weight: 700; line-height: 1.1; letter-spacing: 0.5px; }
  .holder__role { color: var(--ink-warm); font-size: 25px; font-weight: 400; line-height: 1; }

  .mist-disc {
    position: absolute; left: 3px; top: 240px;
    width: 270px; height: 270px; border-radius: 50%;
    background: var(--mist);
  }
  .rule { position: absolute; left: 0; width: 712px; height: 1px; background: var(--rule); }
  .rule--top { top: 176px; }
  .rule--bottom { top: 318px; }

  .field { position: absolute; top: 156px; }
  .field__label { font-size: 12px; font-weight: 700; color: var(--ink-label); letter-spacing: 0.3px; }
  .field__value {
    position: absolute; top: 47px; left: 0;
    background: var(--brand-blue); color: #fff;
    font-size: 14px; line-height: 18px; padding: 6px 8px;
    white-space: nowrap;
  }
  .field__value::before {
    content: ""; position: absolute; top: -11px; left: 13px;
    border-left: 9px solid transparent; border-right: 9px solid transparent;
    border-bottom: 11px solid var(--brand-blue);
  }
  .field--email { left: 35px; }
  .field--web { left: 208px; }
  .field--contact { left: 381px; }
  .field--address { left: 541px; }
  .field--email .field__value { width: 159px; }
  .field--web .field__value { width: 159px; }
  .field--contact .field__value { width: 147px; padding-left: 11px; }
  .field--address .field__value { width: 148px; padding: 6px 10px; }
</style>
</head>
<body>
  <section class="card card--back" aria-label="Card back">
    <div class="brand">
      <span class="brand__dot"></span>
      <div class="brand__text">
        <span class="brand__name">frostkarta</span>
        <span class="brand__tagline">WEB DESIGN &amp; CONSULTANCY</span>
      </div>
    </div>
  </section>

  <section class="card card--front" aria-label="Card front">
    <span class="mist-disc" role="img" aria-label="Large faint brand circle in pale blue"></span>
    <div class="brand">
      <span class="brand__dot"></span>
      <div class="brand__text">
        <span class="brand__name">frostkarta</span>
        <span class="brand__tagline">WEB DESIGN &amp; CONSULTANCY</span>
      </div>
    </div>
    <div class="holder">
      <p class="holder__name">Derek Havill</p>
      <p class="holder__role">Founder</p>
    </div>
    <span class="rule rule--top"></span>
    <span class="rule rule--bottom"></span>
    <div class="field field--email">
      <p class="field__label">EMAIL</p>
      <p class="field__value">www.frostkarta.com.sg</p>
    </div>
    <div class="field field--web">
      <p class="field__label">WEB SITE</p>
      <p class="field__value">hello@frostkarta.com.sg</p>
    </div>
    <div class="field field--contact">
      <p class="field__label">CONTACT</p>
      <p class="field__value">+65&nbsp; 9356 8214</p>
    </div>
    <div class="field field--address">
      <p class="field__label">ADDRESS</p>
      <p class="field__value">7 Marlowfern Lane,<br>#09-14 Tavenport Crest,<br>Singapore 318547</p>
    </div>
  </section>
</body>
</html>
```